we can communicate on this, but i want to follow the approach we took on Pellew|Marsh & Quinlan but i feel the card front needs the black background and the platinum and gold logo. The back? I am open. we can use the same info from PM&Q. Velmont Arc is an enhanced equity investment fund - basically a very exclusive boutique hedge fund that uses only stock options. very advanced things. hope you are interested

Contact Information for Business Card

Dr. Lewis T. Brennick, CFA
Scientifique de fusée financière
701.555.0143
LTBquant47@mailvantor.com

4718 Willow Creek Bend W.
West Fargo, ND 58078

No web site

Colors

Designer to choose colors to be used in the design.

Requirements
Nice to have
• I tend to prefer the most visible applications of the logo to include logo and name, the logo version with a black background and the gold and platinum components separated by the black. I see this working well for a single side (logo and name - this is card front to me).
• I am fairly open to other treatments on the reverse side with the data. To me, it makes sense to have a different color rendition of the logo on the reverse and it may be a muted black tone on tone or an oversized portion that would have spot UV. Or, the reverse may play with colors and layout
Should not have
• Other colors = no no
• Decorative font

```html
<!DOCTYPE html>
<html lang="en">
<head>
<meta charset="utf-8">
<title>Velmont Arc — Business Card</title>
<link href="https://fonts.googleapis.com/css2?family=Montserrat:wght@700&family=Open+Sans:wght@600;700&family=Roboto:wght@400&display=swap" rel="stylesheet">
<style>
  :root {
    --backdrop: #2a2a2b;
    --card: #151517;
    --gold: #d2ad4c;
    --white: #ffffff;
  }
  * { box-sizing: border-box; margin: 0; padding: 0; }
  html, body {
    width: 1200px; height: 900px; overflow: hidden;
    background: var(--backdrop);
  }
  .stage { position: relative; width: 1200px; height: 900px; }
  .card {
    position: absolute;
    width: 680px; height: 380px;
    background: var(--card);
    border-radius: 26px;
    overflow: hidden;
  }
  .card--front { left: 440px; top: 50px; }
  .card--back  { left: 80px;  top: 470px; }

  .brand { display: flex; flex-direction: column; align-items: center; }
  .brand__dot { border-radius: 50%; background: var(--gold); }
  .brand__name {
    font-family: "Montserrat", sans-serif; font-weight: 700;
    color: var(--white); letter-spacing: 1px; white-space: nowrap;
  }
  .card--front .brand {
    position: absolute; left: 0; right: 0; top: 78px;
  }
  .card--front .brand__dot { width: 130px; height: 130px; margin-bottom: 22px; }
  .card--front .brand__name { font-size: 46px; }

  .card--back .brand {
    position: absolute; left: 40px; top: 30px; width: 280px;
  }
  .card--back .brand__dot { width: 100px; height: 100px; margin-bottom: 12px; }
  .card--back .brand__name { font-size: 32px; }

  .contact {
    position: absolute; left: 56px; top: 226px;
    font-family: "Roboto", sans-serif; color: var(--white);
    font-size: 17px; line-height: 1.35; white-space: nowrap;
  }
  .contact__address { margin-bottom: 12px; }
  .contact__row { display: flex; align-items: center; gap: 10px; margin-bottom: 6px; }
  .contact__icon { width: 16px; height: 16px; flex: none; }

  .person {
    position: absolute; right: 58px; top: 200px; text-align: right;
    font-family: "Open Sans", sans-serif; white-space: nowrap;
  }
  .person__name { color: var(--gold); font-weight: 700; font-size: 22px; letter-spacing: 0.5px; }
  .person__title { color: var(--white); font-weight: 600; font-size: 17px; margin-top: 4px; }
  .accent-bar {
    position: absolute; right: 26px; top: 210px;
    width: 18px; height: 64px; background: var(--gold);
  }
</style>
</head>
<body>
<main class="stage">
  <section class="card card--front">
    <div class="brand">
      <div class="brand__dot"></div>
      <div class="brand__name">VELMONT ARC</div>
    </div>
  </section>

  <section class="card card--back">
    <div class="brand">
      <div class="brand__dot"></div>
      <div class="brand__name">VELMONT ARC</div>
    </div>

    <div class="contact">
      <p class="contact__address">4718 Willow Creek Bend W.<br>West Fargo, ND 58078</p>
      <p class="contact__row">
        <svg class="contact__icon" viewBox="0 0 16 16"><path d="M3 1.5l3 .5 1 3.5-2 1.2a8 8 0 0 0 4.3 4.3l1.2-2 3.5 1 .5 3-2 1.5C6.5 14.5 1.5 9.5 1.5 3.5z" fill="var(--gold)"/></svg>
        701.555.0143
      </p>
      <p class="contact__row">
        <svg class="contact__icon" viewBox="0 0 16 16"><rect x="1" y="3" width="14" height="10" fill="none" stroke="var(--gold)" stroke-width="1.8"/><path d="M1.5 3.5L8 9l6.5-5.5" fill="none" stroke="var(--gold)" stroke-width="1.8"/></svg>
        LTBquant47@mailvantor.com
      </p>
    </div>

    <div class="person">
      <p class="person__name">Dr. Lewis T. Brennick, CFA</p>
      <p class="person__title">Scientifique de fusée financière</p>
    </div>
    <div class="accent-bar"></div>
  </section>
</main>
</body>
</html>
```